Business Card Design Project

Industry/Entity Type

Business

Contact Information for Business Card

The Ardenfield Gospel Choir
Desmond Fairley, Minister of Music

The Grace Harbor Fellowship of Mount Orla
Founded 1792

Twitter @ardenfieldchoir
Instagram ardenfieldgc
Facebook socialhub-net.com/afgc382
Website: ardenfieldgc.org
For Bookings: (555) 274-AFGC
2748 Merrow Street, Philadelphia, PA 19151

Back of the Card
Music and Cd's Recordings Available On
Choirs Website and Also
Tunevault, Corvex Sound, Disc Sprout (the music online logo)

```html
<!DOCTYPE html>
<html lang="en">
<head>
<meta charset="utf-8">
<title>The Ardenfield Gospel Choir – Business Card</title>
<link href="https://fonts.googleapis.com/css2?family=Roboto:wght@400;700&family=Cormorant+Garamond:ital,wght@1,500;1,600&display=swap" rel="stylesheet">
<style>
  :root {
    --bg: #ecebe8;
    --blue-deep: #165aa3;
    --blue-light: #3f86c6;
    --white: #ffffff;
    --paper: #fbfbfb;
    --ink-soft: rgba(255,255,255,0.55);
    --red: #d23b3b;
    --pill: #7fb3df;
    --ink: #2b2b2b;
  }
  * { margin: 0; padding: 0; box-sizing: border-box; }
  html, body { width: 1200px; height: 911px; overflow: hidden; background: var(--bg); }
  .canvas { position: relative; width: 1200px; height: 911px; }
  .card {
    position: absolute; width: 560px; height: 320px; border-radius: 20px;
    box-shadow: 0 10px 28px rgba(0,0,0,0.18); overflow: hidden;
  }
  .card-front {
    left: 26px; top: 296px;
    background: linear-gradient(120deg, var(--blue-deep) 0%, var(--blue-deep) 45%, var(--blue-light) 100%);
    color: var(--white); font-family: "Roboto", sans-serif;
  }
  .contact-column { position: absolute; left: 40px; top: 40px; width: 230px; }
  .holder-name { font-size: 24px; font-weight: 700; letter-spacing: 0.5px; line-height: 1; }
  .holder-title { font-size: 14px; margin-top: 4px; }
  .divider { border-top: 1px dashed var(--ink-soft); margin: 18px 0; width: 200px; }
  .address { font-size: 13px; line-height: 1.4; }
  .social-list { list-style: none; font-size: 12.5px; line-height: 1.55; }
  .social-list li { display: flex; align-items: center; gap: 8px; }
  .social-list .bullet { width: 10px; height: 10px; border-radius: 50%; background: var(--white); flex: none; }
  .social-list svg { width: 10px; height: 10px; flex: none; }
  .choir-block { position: absolute; right: 30px; top: 48px; width: 250px; text-align: center; }
  .crest-mark { display: flex; align-items: center; justify-content: center; gap: 8px; height: 70px; font-size: 18px; font-weight: 700; }
  .crest-mark .dot { width: 14px; height: 14px; border-radius: 50%; background: var(--white); }
  .choir-name { font-family: "Cormorant Garamond", serif; font-style: italic; font-weight: 600; font-size: 21px; margin-top: 10px; }
  .minister { font-size: 13px; font-weight: 700; margin-top: 4px; }
  .church { font-size: 10px; margin-top: 6px; }
  .founded { font-size: 10px; margin-top: 2px; }

  .card-back {
    left: 612px; top: 296px; background: var(--paper);
    font-family: "Roboto", sans-serif; text-align: center;
  }
  .back-mark { display: flex; align-items: center; justify-content: center; gap: 8px; margin-top: 42px; font-size: 20px; font-weight: 700; color: var(--ink); }
  .back-mark .dot { width: 14px; height: 14px; border-radius: 50%; background: var(--ink); }
  .availability { font-family: "Cormorant Garamond", serif; font-style: italic; font-weight: 500; color: var(--red); font-size: 22px; line-height: 1.25; margin-top: 30px; }
  .store-list { list-style: none; display: flex; justify-content: center; gap: 16px; margin-top: 34px; }
  .store-list li {
    border: 1.5px solid var(--pill); border-radius: 16px; padding: 6px 16px;
    font-size: 13px; font-weight: 700; color: var(--ink);
  }
</style>
</head>
<body>
<div class="canvas">
  <section class="card card-front">
    <div class="contact-column">
      <div class="holder-name">JORDAN VALE</div>
      <div class="holder-title">CEO/FOUNDER</div>
      <div class="divider"></div>
      <div class="address">2748 Merrow Street<br>Philadelphia, PA 19151</div>
      <div class="divider"></div>
      <ul class="social-list">
        <li><span class="bullet"></span>@ardenfieldchoir</li>
        <li><span class="bullet"></span>ardenfieldgc</li>
        <li><span class="bullet"></span>/afgc382</li>
        <li><svg viewBox="0 0 10 10"><path d="M2 1h2l1 2-1.2 1a5 5 0 0 0 2.2 2.2L7 5l2 1v2a1 1 0 0 1-1 1A8 8 0 0 1 1 2a1 1 0 0 1 1-1z" fill="#fff"/></svg>(555) 274-AFGC (Bookings)</li>
        <li><svg viewBox="0 0 10 10"><circle cx="5" cy="5" r="4.3" fill="none" stroke="#fff" stroke-width="1.2"/><path d="M0.7 5h8.6M5 0.7c-2 2.5-2 6.1 0 8.6M5 0.7c2 2.5 2 6.1 0 8.6" fill="none" stroke="#fff" stroke-width="0.9"/></svg>www.ardenfieldgc.org</li>
      </ul>
    </div>
    <div class="choir-block">
      <div class="crest-mark"><span class="dot"></span>Ardenfield</div>
      <div class="choir-name">The Ardenfield Gospel Choir</div>
      <div class="minister">Desmond Fairley, Minister of Music</div>
      <div class="church">The Grace Harbor Fellowship of Mount Orla</div>
      <div class="founded">Founded 1792</div>
    </div>
  </section>

  <section class="card card-back">
    <div class="back-mark"><span class="dot"></span>Ardenfield</div>
    <p class="availability">Music and Cd's Recordings Available On<br>Choirs Website and Also</p>
    <ul class="store-list">
      <li>Tunevault</li>
      <li>Corvex Sound</li>
      <li>Disc Sprout</li>
    </ul>
  </section>
</div>
</body>
</html>
```